Newsletter Ad

I am looking for someone to design an advertisement for a mother's club newsletter. 4" wide X by 5" tall (and 2.5" wide X 5" tall if possible).

I'm a psychotherapist, so want the ad to look professional, but modern. I have a logo with my photo attached that can be incorporated into the design. The colors of my website are turquoise and white. I'd like to keep with that theme...so maybe some turquoise blocking to match the logo font color.

I'm uploading a logo as well as an ad draft with the content I'd like listed in the ad.

```html
<!DOCTYPE html>
<html lang="en">
<head>
<meta charset="utf-8">
<title>Mara Lindell, MA, MFT – Newsletter Ad</title>
<link rel="stylesheet" href="https://fonts.googleapis.com/css2?family=Questrial&family=Roboto+Condensed:wght@400;700&display=swap">
<style>
  :root {
    --teal: #4aa3a2;
    --ink: #333333;
    --paper: #ffffff;
    --portrait-dark: #2a2522;
    --portrait-warm: #9a7a5e;
  }
  html, body {
    margin: 0;
    padding: 0;
    width: 1200px;
    height: 2386px;
    overflow: hidden;
    background: var(--paper);
  }
  .ad {
    position: relative;
    width: 1200px;
    height: 2386px;
    box-sizing: border-box;
    border: 12px solid var(--teal);
    background: var(--paper);
    font-family: "Roboto Condensed", "Arial Narrow", sans-serif;
    color: var(--ink);
  }
  .ad > * { position: absolute; margin: 0; line-height: 1; }
  .portrait {
    left: 44px; top: 40px; width: 428px; height: 432px;
    background: radial-gradient(ellipse at 55% 50%, var(--portrait-warm) 0%, #6b5140 38%, var(--portrait-dark) 75%);
  }
  .name {
    right: 64px; top: 130px;
    font-family: "Questrial", sans-serif;
    font-size: 82px; font-weight: 400; color: var(--teal);
    letter-spacing: 2px;
    white-space: nowrap;
  }
  .credentials {
    right: 64px; top: 250px;
    font-family: "Questrial", sans-serif;
    font-size: 76px; color: var(--teal);
    letter-spacing: 2px;
  }
  .license {
    right: 20px; top: 430px;
    font-size: 58px; color: var(--teal);
  }
  .headline {
    left: 0; right: 0; top: 580px;
    text-align: center;
    font-size: 92px; line-height: 118px;
    font-weight: 400;
  }
  .specialties { left: 0; top: 0; width: 1176px; height: 2362px; }
  .specialties text {
    font-family: "Roboto Condensed", sans-serif;
    font-size: 72px; fill: var(--ink);
    text-anchor: middle;
  }
  .specialties line { stroke: var(--teal); stroke-width: 5; }
  .call {
    left: 0; right: 0; top: 1898px;
    text-align: center;
    font-size: 92px; font-weight: 700; color: var(--teal);
  }
  .phone {
    left: 0; right: 0; top: 1996px;
    text-align: center;
    font-size: 106px; font-weight: 700; color: var(--teal);
  }
  .contact {
    left: 0; right: 0; top: 2176px;
    text-align: center;
    font-size: 62px; line-height: 72px;
    font-style: normal;
  }
  .contact .web { margin-right: 36px; }
</style>
</head>
<body>
<div class="ad">
  <div class="portrait" role="img" aria-label="Portrait photograph of the therapist against a dark background"></div>
  <h1 class="name">MARA LINDELL</h1>
  <p class="credentials">MA, MFT</p>
  <p class="license">License# MFC48203</p>
  <h2 class="headline">Psychotherapy for Individuals<br>Couples and Families</h2>
  <svg class="specialties" viewBox="0 0 1176 2362" aria-label="Areas of focus">
    <text x="588" y="912">Anxiety</text>
    <line x1="454" y1="942" x2="728" y2="942"/>
    <text x="588" y="1026">Divorce</text>
    <line x1="428" y1="1048" x2="752" y2="1048"/>
    <text x="588" y="1146">Parenting</text>
    <line x1="398" y1="1174" x2="784" y2="1174"/>
    <text x="588" y="1268">Depression</text>
    <line x1="372" y1="1300" x2="808" y2="1300"/>
    <text x="588" y="1394">Couples Issues</text>
    <line x1="358" y1="1448" x2="824" y2="1448"/>
    <text x="588" y="1548">Life Transitions</text>
    <line x1="324" y1="1582" x2="856" y2="1582"/>
    <text x="588" y="1668">Women’s Issues</text>
    <line x1="180" y1="1702" x2="1000" y2="1702"/>
    <text x="588" y="1794">Attachment &amp; Neuroscience</text>
  </svg>
  <p class="call">Call Now</p>
  <p class="phone">415 555 0186</p>
  <address class="contact">
    118 Alder Lane, Fairbrook, CA 94900<br>
    <span class="web">www.maralindell.com</span><span class="email">mara@maralindell.com</span>
  </address>
</div>
</body>
</html>
```